Zolvana Stationary and Branding Documents

Corporate Identity Branding stationary needed for IT Recruiting Firm.

I already have a Logo, business cards and website. I need to get designs completed for the remaining corporate identity documents.

The documentation should use similar colors as my website and business card. The designs should modern and clean.

http://zolvanaworks.example/

Target Market(s)

Information Technology Industry

Industry/Entity Type

Information Technology

Colors
3377b5
0255a3
fbee3e
f78f20
f37122
33a6d7
000000
0592cd

Requirements
Must have
• Letter Head
• Folder Design
• PowerPoint Design
• Invoice
• Envelope
Nice to have
• Proposal
• Flyer
• Brochure
Should not have
• Logo
• Business Cards
• Website

```html
<!DOCTYPE html>
<html lang="en">
<head>
<meta charset="utf-8">
<title>Zolvana Stationery Set</title>
<link href="https://fonts.googleapis.com/css2?family=Quicksand:wght@400;500;600&family=Open+Sans:wght@400;600;700&family=Cinzel:wght@500&display=swap" rel="stylesheet">
<style>
:root{
  --blue:#0255a3;
  --blue-mid:#1c78c0;
  --blue-light:#3377b5;
  --orange:#f37122;
  --orange-soft:#f78f20;
  --charcoal:#2b2b2b;
  --grey:#e4e4e4;
  --grey-line:#cfcfcf;
  --text:#555;
  --paper:#ffffff;
  --bg:#f4f4f4;
}
*{box-sizing:border-box;margin:0;padding:0}
html,body{width:1200px;height:1200px;overflow:hidden;background:var(--bg)}
body{position:relative;font-family:"Open Sans",sans-serif;color:var(--text)}
.sheet{position:absolute;background:var(--paper);overflow:hidden}
.brand-name{font-family:"Quicksand",sans-serif;font-weight:500;color:var(--blue);letter-spacing:.5px;line-height:1}
.swoosh{position:absolute;left:0;bottom:0;width:100%}
.site-url{position:absolute;color:#fff;font-weight:700}

/* letterhead */
.letterhead{left:76px;top:42px;width:380px;height:538px}
.letterhead .brand-name{position:absolute;left:27px;top:30px;font-size:24px}
.letterhead .rule{position:absolute;left:139px;right:40px;top:53px;height:1px;background:var(--blue-light)}
.letterhead .contact{position:absolute;right:40px;top:44px;text-align:right;font-size:4.5px;line-height:1.9}
.letterhead .contact .addr{color:var(--orange);font-weight:700;position:absolute;right:0;top:-4px;white-space:nowrap}
.letterhead .contact .lines{position:absolute;right:0;top:10px;white-space:nowrap;color:var(--blue)}
.letterhead .site-url{right:12px;bottom:10px;font-size:6px}

/* invoice */
.invoice{left:498px;top:38px;width:416px;height:538px}
.invoice .brand-name{position:absolute;right:38px;top:42px;font-size:27px}
.invoice-title{position:absolute;left:39px;top:90px;font-family:"Quicksand",sans-serif;color:var(--orange);font-size:14px;font-weight:500}
.invoice-title b{font-size:19px;font-weight:500}
.invoice-dates{position:absolute;left:39px;top:113px;font-size:5.5px;line-height:1.5;color:#888}
.parties{position:absolute;left:39px;top:133px;width:338px;height:76px;border:1px solid var(--orange);display:flex}
.party{flex:1;padding:2px}
.party + .party{border-left:1px solid var(--orange)}
.party-head{background:var(--blue);color:#fff;font-size:7px;padding:4px 6px;height:19px;border-radius:2px}
.party-body{display:flex;gap:4px;margin-top:3px}
.party-logo{width:40px;height:34px;border:1px solid var(--grey);display:flex;align-items:center;justify-content:center;font-family:"Quicksand",sans-serif;font-size:8px;color:var(--blue);font-weight:500}
.party-logo.blank{color:#ddd}
.party-fields{flex:1;display:flex;flex-direction:column;gap:2px}
.party-fields span{background:#eee;font-size:4.5px;height:7.5px;padding-left:2px;line-height:7.5px}
.items-label{position:absolute;left:42px;top:217px;font-size:7px}
.items{position:absolute;left:39px;top:230px;width:338px;border-collapse:separate;border-spacing:0 3px;font-size:5px}
.items th{background:var(--orange);color:#fff;font-weight:400;height:19px;text-align:left;padding:0 8px}
.items th.num,.items td.num{text-align:center}
.items td{background:var(--grey);height:20px;padding:0 8px;border-right:1px solid #fff}
.notes{position:absolute;left:39px;top:409px;width:218px;height:66px;border:1px solid var(--grey);padding:9px 6px;font-size:5.5px}
.notes i{display:block;border-bottom:1px solid #eee;height:8px}
.notes-foot{position:absolute;left:42px;top:482px;font-size:4px}
.amount{position:absolute;left:271px;top:404px;width:104px;font-size:5px}
.amount-head{background:var(--blue);color:#fff;text-align:center;font-size:8px;height:19px;line-height:19px}
.amount-row{display:flex;border-bottom:1px solid var(--grey);height:17px;align-items:center}
.amount-row span{flex:1;text-align:right;padding-right:4px}
.amount-row span+span{border-left:1px solid var(--grey)}
.amount-total{display:flex;justify-content:flex-end;align-items:baseline;gap:3px;padding-top:3px}
.amount-total b{font-family:"Quicksand",sans-serif;font-weight:400;font-size:11px;color:#444}

/* folder */
.folder{left:73px;top:596px;width:433px;height:574px;background:var(--blue-mid)}
.folder-photo{position:absolute;left:0;top:0;width:100%;height:265px;background:linear-gradient(135deg,#9fd2ea 0%,#e9f3f8 45%,#c9e0ec 70%,#7fb3d3 100%)}
.folder .brand-name{position:absolute;left:0;right:0;top:418px;text-align:center;color:#fff;font-size:52px}
.folder-band{position:absolute;left:0;right:0;top:505px;height:20px;background:linear-gradient(#f78f20,#e0661a);color:#fff;text-align:center;font-family:"Cinzel",serif;font-size:14px;line-height:20px;letter-spacing:1px}
.folder-foot{position:absolute;left:0;right:0;top:561px;height:2px;background:#cfe0ee}
.folder-foot span{position:absolute;left:50%;top:-6px;transform:translateX(-50%);background:#3a5f8c;color:#fff;font-size:8px;font-weight:700;padding:2px 8px;border-radius:6px}

/* envelope front */
.env-front{left:551px;top:602px;width:582px;height:292px}
.env-front .brand-name{position:absolute;left:20px;top:22px;font-size:34px}
.env-front .rule{position:absolute;left:26px;top:66px;width:150px;height:1px;background:var(--blue-light)}
.env-front .addr{position:absolute;left:38px;top:72px;font-size:7px;color:var(--orange);font-weight:700}
.env-front .lines{position:absolute;left:32px;top:83px;font-size:6.5px;color:var(--blue)}
.env-front .site-url{right:26px;bottom:14px;font-size:9px}

/* envelope back */
.env-back{left:551px;top:910px;width:586px;height:275px;background:var(--blue)}
</style>
</head>
<body>

<section class="sheet letterhead" aria-label="Letterhead">
  <div class="brand-name">zolvana</div>
  <div class="rule"></div>
  <div class="contact">
    <div class="addr">Four Harbor Plaza 210, 9th Street SW</div>
    <div class="lines">☎ 5550142287 ✉ info@zolvanaworks.example</div>
  </div>
  <svg class="swoosh" viewBox="0 0 380 56" height="56" preserveAspectRatio="none">
    <polygon points="0,12 380,12 380,56 0,56" fill="none"/>
    <polygon points="0,12 210,21 380,21 380,56 0,56" fill="var(--charcoal)"/>
    <polygon points="20,56 380,0 380,56" fill="var(--blue)"/>
    <polygon points="180,20 260,20 200,24" fill="var(--orange)"/>
  </svg>
  <div class="site-url">www.zolvanaworks.example</div>
</section>

<section class="sheet invoice" aria-label="Invoice">
  <div class="brand-name">zolvana</div>
  <div class="invoice-title">Invoice <b>0001</b></div>
  <div class="invoice-dates">01 September , 2012<br>Payment due by 25 November 2012</div>
  <div class="parties">
    <div class="party">
      <div class="party-head">FROM</div>
      <div class="party-body">
        <div class="party-logo">zolvana</div>
        <div class="party-fields"><span>Your Address</span><span>Address Line 1</span><span>Town</span><span>Region/State</span><span>Zip/Postal Code</span></div>
      </div>
    </div>
    <div class="party">
      <div class="party-head">TO</div>
      <div class="party-body">
        <div class="party-logo blank">LOGO</div>
        <div class="party-fields"><span>Your Address</span><span>Address Line 1</span><span>Town</span><span>Region/State</span><span>Zip/Postal Code</span></div>
      </div>
    </div>
  </div>
  <div class="items-label">ITEMS</div>
  <table class="items">
    <thead><tr><th class="num">Quantity</th><th>Description</th><th class="num">Unit Price</th><th class="num">TOTAL</th></tr></thead>
    <tbody>
      <tr><td class="num">2</td><td>Donec ac erat vel neque molestie convallis.</td><td class="num">$600</td><td class="num">$1200</td></tr>
      <tr><td class="num">1</td><td>Sed eget risus ac lacus tempus sollicitudin in at magna.</td><td class="num">$300</td><td class="num">$300</td></tr>
      <tr><td class="num">3</td><td>Nunc auctor nisl vel lorem aliquet pellentesque.</td><td class="num">$800</td><td class="num">$2400</td></tr>
      <tr><td class="num">2</td><td>Pellentesque habitant morbi.</td><td class="num">$20</td><td class="num">$40</td></tr>
      <tr><td class="num">2</td><td>In hac habitasse platea dictumst mauris at.</td><td class="num">$2500</td><td class="num">$5000</td></tr>
      <tr><td class="num">1</td><td>Aenean eget enim eget augue dictum fringilla et vitae.</td><td class="num">$100</td><td class="num">$100</td></tr>
    </tbody>
  </table>
  <div class="notes">Special Notes<i></i><i></i><i></i></div>
  <div class="notes-foot">molestie condimentum. Curabitur mi dui, faucibus sed</div>
  <div class="amount">
    <div class="amount-head">AMOUNT DUE</div>
    <div class="amount-row"><span>SUBTOTAL</span><span>$9,040</span></div>
    <div class="amount-row"><span>TAX</span><span>$00.00</span></div>
    <div class="amount-row"><span>SHIPPING</span><span>$00.00</span></div>
    <div class="amount-total">TOTAL <b>$9,040.00</b></div>
  </div>
  <svg class="swoosh" viewBox="0 0 416 48" height="48" preserveAspectRatio="none">
    <polygon points="0,12 230,25 416,25 416,48 0,48" fill="var(--charcoal)"/>
    <polygon points="100,48 416,0 416,48" fill="var(--blue)"/>
    <polygon points="200,24 290,24 225,28" fill="var(--orange)"/>
  </svg>
</section>

<section class="sheet folder" aria-label="Presentation folder">
  <div class="folder-photo" role="img" aria-label="Photo of a business team meeting around a laptop in a bright office"></div>
  <svg style="position:absolute;left:0;top:240px" width="433" height="100" viewBox="0 0 433 100" preserveAspectRatio="none">
    <path d="M0,25 L0,0 L433,0 L433,20 C330,-5 150,-10 0,25Z" fill="#e9f3f8"/>
    <path d="M0,58 C110,-5 320,-5 433,40 L433,20 C330,-5 150,-10 0,25Z" fill="var(--orange)"/>
    <path d="M0,62 C120,15 300,15 433,55 L433,40 C320,-5 110,-5 0,58Z" fill="#f2f4f6"/>
    <path d="M0,100 L0,62 C120,15 300,15 433,55 L433,100Z" fill="var(--blue-mid)"/>
  </svg>
  <div class="brand-name">zolvana</div>
  <div class="folder-band">JOIN THE ELITE</div>
  <div class="folder-foot"><span>zolvanaworks.example</span></div>
</section>

<section class="sheet env-front" aria-label="Envelope front">
  <div class="brand-name">zolvana</div>
  <div class="rule"></div>
  <div class="addr">Four Harbor Plaza 210, 9th Street SW</div>
  <div class="lines">☎ 5550142287 ✉ info@zolvanaworks.example</div>
  <svg class="swoosh" viewBox="0 0 582 92" height="92" preserveAspectRatio="none">
    <polygon points="0,22 360,44 582,44 582,92 0,92" fill="var(--charcoal)"/>
    <polygon points="100,92 582,0 582,92" fill="var(--blue)"/>
    <polygon points="300,40 400,40 340,45" fill="var(--orange)"/>
  </svg>
  <div class="site-url">www.zolvanaworks.example</div>
</section>

<section class="sheet env-back" aria-label="Envelope back">
  <svg width="586" height="275" viewBox="0 0 586 275">
    <path d="M8,4 L40,125 Q45,140 65,140 L521,140 Q541,140 546,125 L578,4" fill="none" stroke="#0a4a8c" stroke-width="2"/>
    <path d="M8,271 L200,150 M578,271 L386,150" stroke="#0a4a8c" stroke-width="1.5" opacity=".6"/>
  </svg>
</section>

</body>
</html>
```